Hartwell Estates Business Cards

I would like a business card that includes myself and my partner.
Includes: Logo, office #, email, website, our names, our numbers and possibly the address. I would also like the logo to be embossed and the card to be horizontal.
There is a photo of our yard signs to give you an idea of the colors of our business.

Target Market(s)

Everyone in real estate market.
We are in a rural area. Our clientele are from all socioeconomic backgrounds.

Industry/Entity Type

Real Estate Agent

Contact Information for Business Card

Company Name: Hartwell Estates
Our Names, Titles & Cell #'s : Dana Pembrook-Broker (555).317.6624, Marla Pembrook-Realtor (555).609.1385
Office #: (555).240.3918
Website: hartwellestates-demo.com
Joint Email: pembrook@hartwellestates-demo.com
Office Address: 418B W. Calloway Ave.
Cedar Bend, TX. 70913

Font styles to use
Serif

Requirements
Must have
• HORIZONTAL, Logo, Myself and my partners names, Our cell #'s, our office #, our website, our email address
Nice to have
• Embossed logo, office address, our titles.

```html
<!DOCTYPE html>
<html lang="en">
<head>
<meta charset="utf-8">
<title>Hartwell Estates – Business Card</title>
<link rel="stylesheet" href="https://fonts.googleapis.com/css2?family=Libre+Baskerville:wght@400;700&display=swap">
<style>
  :root {
    --paper: #ffffff;
    --skyline: #eceef0;
    --brand: #4a2262;
    --band: #4b2364;
    --band-edge: #3a1850;
    --ink-light: #ffffff;
    --divider: rgba(255,255,255,0.45);
  }
  * { margin: 0; padding: 0; box-sizing: border-box; }
  html, body { width: 1200px; height: 720px; overflow: hidden; background: var(--paper); }
  .card {
    position: relative;
    width: 1200px; height: 720px;
    background: var(--paper);
    font-family: "Libre Baskerville", Georgia, serif;
    overflow: hidden;
  }
  .skyline {
    position: absolute; left: 0; top: 50px; width: 1200px; height: 310px;
    background: linear-gradient(180deg, rgba(236,238,240,0) 0%, var(--skyline) 45%, var(--skyline) 100%);
  }
  .band { position: absolute; inset: 0; }
  .brand {
    position: absolute; left: 0; top: 150px; width: 1200px;
    display: flex; align-items: center; justify-content: center; gap: 26px;
    color: var(--brand);
  }
  .brand-mark { width: 70px; height: 70px; border-radius: 50%; background: var(--brand); }
  .brand-name { font-size: 58px; font-weight: 700; letter-spacing: 1px; }
  .agent {
    position: absolute; top: 374px; width: 460px; text-align: center;
    color: var(--ink-light); font-weight: 700;
  }
  .agent-left { left: 117px; }
  .agent-right { left: 602px; }
  .agent-name { font-size: 31px; letter-spacing: 2px; text-transform: uppercase; line-height: 40px; }
  .agent-title { font-size: 21px; line-height: 32px; margin-top: 2px; }
  .agent-phone { font-size: 23px; letter-spacing: 1px; line-height: 34px; }
  .agent-divider {
    position: absolute; left: 582px; top: 378px; width: 1px; height: 95px; background: var(--divider);
  }
  .contact {
    position: absolute; display: flex; align-items: center; gap: 14px;
    color: var(--ink-light); font-size: 19.5px; font-weight: 700; letter-spacing: 1px;
    white-space: nowrap;
  }
  .contact-icon { width: 36px; height: 36px; flex: none; }
  .office-phone { left: 85px; top: 538px; }
  .website { left: 85px; top: 599px; }
  .email { left: 503px; top: 540px; }
  .address { left: 503px; top: 599px; }
</style>
</head>
<body>
<div class="card">
  <div class="skyline" role="img" aria-label="Faint grey city skyline silhouette"></div>

  <svg class="band" width="1200" height="720" viewBox="0 0 1200 720">
    <path d="M0,345 Q600,216 1200,345 L1200,720 L0,720 Z" fill="var(--band-edge)"/>
    <path d="M0,357 Q600,230 1200,357 L1200,720 L0,720 Z" fill="var(--band)"/>
  </svg>

  <div class="brand">
    <span class="brand-mark"></span>
    <span class="brand-name">Hartwell Estates</span>
  </div>

  <div class="agent agent-left">
    <div class="agent-name">Dana Pembrook</div>
    <div class="agent-title">Broker</div>
    <div class="agent-phone">(555).317.6624</div>
  </div>
  <div class="agent-divider"></div>
  <div class="agent agent-right">
    <div class="agent-name">Marla Pembrook</div>
    <div class="agent-title">Realtor</div>
    <div class="agent-phone">(555).609.1385</div>
  </div>

  <div class="contact office-phone">
    <svg class="contact-icon" viewBox="0 0 36 36">
      <circle cx="18" cy="18" r="18" fill="#fff"/>
      <rect x="11" y="9" width="14" height="18" rx="3" fill="var(--band)"/>
      <path d="M15 13c-1 2 1 7 5 9l1.6-1.6-2-1.5-1 .8c-1.2-.7-2.2-2-2.5-3.3l1-.8-1-2.2z" fill="#fff"/>
    </svg>
    <span>(555).240.3918</span>
  </div>
  <div class="contact website">
    <svg class="contact-icon" viewBox="0 0 36 36">
      <circle cx="18" cy="18" r="18" fill="#fff"/>
      <g fill="none" stroke="var(--band)" stroke-width="1.8">
        <circle cx="18" cy="18" r="9"/>
        <ellipse cx="18" cy="18" rx="4" ry="9"/>
        <path d="M9 18h18M10.5 13.5h15M10.5 22.5h15"/>
      </g>
    </svg>
    <span>hartwellestates-demo.com</span>
  </div>
  <div class="contact email">
    <svg class="contact-icon" viewBox="0 0 36 36">
      <circle cx="18" cy="18" r="18" fill="#fff"/>
      <path d="M9 16l9-6 9 6v10H9z" fill="var(--band)"/>
      <path d="M9 16l9 6 9-6" fill="none" stroke="#fff" stroke-width="1.6"/>
    </svg>
    <span>pembrook@hartwellestates-demo.com</span>
  </div>
  <div class="contact address">
    <svg class="contact-icon" viewBox="0 0 36 36">
      <circle cx="18" cy="18" r="18" fill="#fff"/>
      <path d="M18 8a6.5 6.5 0 0 0-6.5 6.5c0 5 6.5 11.5 6.5 11.5s6.5-6.5 6.5-11.5A6.5 6.5 0 0 0 18 8z" fill="var(--band)"/>
      <circle cx="18" cy="14.5" r="2.4" fill="#fff"/>
      <path d="M12 27.5h12" stroke="var(--band)" stroke-width="1.6"/>
    </svg>
    <span>418B W. Calloway Ave. Cedar Bend, TX. 70913</span>
  </div>
</div>
</body>
</html>
```